Maple Grove Youngsters Guild Business Card Project

We are a Minneapolis based discount club that caters to families with children. We need a business card that can be used to communicate our contact information to other businesses that may wish to offer discounts on our website.

Please use placeholders for contact information (i.e. John Doe, 123 Any Street, Any Town, etc.) and include spaces for the following: Full name, title, email, phone number, website, one line street address, city, state, and zip code.
Updates

Project Deadline Extended
Reason: I have extended the deadline because I had not intended the project to close so quickly.

Target Market(s)

Most of the time the business cards will be used in business to business situations. However, from time to time they may be distributed to our end customer, families with children.

Industry/Entity Type

Club

Font styles to use
Serif
Sans Serif
Other font styles liked:
• Open to suggestions

Requirements
Nice to have
• We might use the reverse side of the card as the design for our membership card.

```html
<!DOCTYPE html>
<html lang="en">
<head>
<meta charset="utf-8">
<title>Maple Grove Youngsters Guild – Business Card</title>
<link rel="stylesheet" href="https://fonts.googleapis.com/css2?family=Arimo:wght@400;700&display=swap">
<style>
  :root {
    --page: #ffffff;
    --card-dark: #1f1c1a;
    --card-mid: #3a3f37;
    --card-green: #55604f;
    --name-red: #c0161c;
    --text-light: #f2f2f2;
    --accent-orange: #f08a1c;
    --brand-yellow: #f7b51e;
  }
  html, body {
    margin: 0;
    padding: 0;
  }
  body {
    width: 987px;
    height: 1200px;
    overflow: hidden;
    background: var(--page);
    position: relative;
    font-family: "Arimo", Arial, sans-serif;
  }
  .card {
    position: absolute;
    overflow: hidden;
    box-sizing: border-box;
  }
  .card--front {
    left: 112px;
    top: 128px;
    width: 776px;
    height: 431px;
  }
  .card--back {
    left: 117px;
    top: 622px;
    width: 748px;
    height: 418px;
  }
  .card__texture {
    position: absolute;
    inset: 0;
    background:
      radial-gradient(ellipse at 30% 35%, rgba(85, 96, 79, 0.85), transparent 60%),
      radial-gradient(ellipse at 75% 70%, rgba(58, 63, 55, 0.9), transparent 65%),
      linear-gradient(135deg, var(--card-mid), var(--card-dark) 55%, var(--card-green));
  }
  .holder {
    position: absolute;
    left: 66px;
    top: 112px;
  }
  .holder__name {
    margin: 0;
    color: var(--name-red);
    font-size: 29px;
    font-weight: 400;
    line-height: 1;
  }
  .holder__title {
    margin: 4px 0 0;
    color: var(--text-light);
    font-size: 19px;
    line-height: 1.2;
  }
  .contact {
    position: absolute;
    left: 66px;
    top: 202px;
    margin: 0;
    padding: 0;
    list-style: none;
  }
  .contact__item {
    display: flex;
    align-items: center;
    height: 28px;
    color: var(--text-light);
    font-size: 17px;
  }
  .contact__icon {
    width: 20px;
    height: 20px;
    margin-right: 12px;
    flex: none;
  }
  .brand {
    position: absolute;
    color: var(--brand-yellow);
    font-weight: 700;
    text-align: center;
    line-height: 1.05;
    display: flex;
    align-items: center;
    gap: 14px;
  }
  .brand__dot {
    width: 26px;
    height: 26px;
    border-radius: 50%;
    background: var(--brand-yellow);
    flex: none;
  }
  .card--front .brand {
    left: 440px;
    top: 170px;
    font-size: 36px;
  }
  .card--back .brand {
    left: 180px;
    top: 140px;
    font-size: 46px;
  }
  .website {
    position: absolute;
    left: 0;
    right: 0;
    top: 374px;
    text-align: center;
    color: var(--accent-orange);
    font-size: 20px;
  }
</style>
</head>
<body>

<section class="card card--front" aria-label="Business card front">
  <div class="card__texture" role="img" aria-label="Dark green-grey grunge background with scratched crossing lines"></div>

  <div class="holder">
    <h1 class="holder__name">Dorian Velasquez</h1>
    <p class="holder__title">Financial Advisor</p>
  </div>

  <ul class="contact">
    <li class="contact__item">
      <svg class="contact__icon" viewBox="0 0 20 20" aria-hidden="true"><circle cx="10" cy="10" r="10" fill="var(--accent-orange)"/><path d="M4.5 10.5 10 5.5l5.5 5h-1.7V15h-2.6v-3H8.8v3H6.2v-4.5z" fill="#fff"/></svg>
      482 harlow street
    </li>
    <li class="contact__item">
      <svg class="contact__icon" viewBox="0 0 20 20" aria-hidden="true"><circle cx="10" cy="10" r="10" fill="var(--accent-orange)"/><path d="M4.5 10.5 10 5.5l5.5 5h-1.7V15h-2.6v-3H8.8v3H6.2v-4.5z" fill="#fff"/></svg>
      minnesota
    </li>
    <li class="contact__item">
      <svg class="contact__icon" viewBox="0 0 20 20" aria-hidden="true"><circle cx="10" cy="10" r="10" fill="var(--accent-orange)"/><rect x="5.5" y="6.5" width="9" height="7" rx="1" fill="#fff"/></svg>
      55418
    </li>
    <li class="contact__item">
      <svg class="contact__icon" viewBox="0 0 20 20" aria-hidden="true"><circle cx="10" cy="10" r="10" fill="var(--accent-orange)"/><rect x="5" y="6.5" width="10" height="7" rx="1" fill="#fff"/><path d="M5 7l5 3.5L15 7" stroke="var(--accent-orange)" stroke-width="1.2" fill="none"/></svg>
      dorian@mgyg.org
    </li>
    <li class="contact__item">
      <svg class="contact__icon" viewBox="0 0 20 20" aria-hidden="true"><circle cx="10" cy="10" r="10" fill="var(--accent-orange)"/><path d="M7 5.5c.6-.3 1.2 0 1.5.6l.7 1.6c.2.5 0 1-.4 1.3l-.6.4c.5 1.2 1.3 2 2.4 2.6l.4-.6c.3-.4.9-.6 1.3-.3l1.5.8c.5.3.7 1 .4 1.5-.7 1.1-2 1.5-3.2.9C8.6 13.1 6.8 11.2 6 8.8c-.4-1.2 0-2.6 1-3.3z" fill="#fff"/></svg>
      03 0442 118 620 7
    </li>
  </ul>

  <div class="brand">
    <span class="brand__dot" aria-hidden="true"></span>
    <span>Maple Grove<br>Youngsters Guild</span>
  </div>
</section>

<section class="card card--back" aria-label="Business card back">
  <div class="card__texture" role="img" aria-label="Dark green-grey grunge background with scratched crossing lines"></div>

  <div class="brand">
    <span class="brand__dot" aria-hidden="true"></span>
    <span>Maple Grove<br>Youngsters Guild</span>
  </div>

  <p class="website">www.maplegroveyoungstersguild.com</p>
</section>

</body>
</html>
```